Veltrane Group Business Card Design

The CEO is looking for a new trendy look for his business card.
You can stay with current branding or come up with something new/creative. It can be 3D, including Medical Office buildings. You can use our logo in a variety of colors. Please include name, title, company name, company website, email address, cell number

Target Market(s)

Real Estate Development and Construction

Industry/Entity Type

Health care real estate

Contact Information for Business Card

Rohesh Kamdar, CEO M-604.781.2249 E-roheshkamdar@veltrane.com Address:4180 Lindqvist Ave, Tampa, FL 33482 www.veltrane.com

Font styles to use
Other font styles liked:
• Be creative

Requirements
Must have
• Creative, trendy look
Nice to have
• Please go to our website to get a feel- www. veltrane.com
Should not have
• small fonts

```html
<!DOCTYPE html>
<html lang="en">
<head>
<meta charset="utf-8">
<title>Veltrane Group – Business Card</title>
<link rel="stylesheet" href="https://fonts.googleapis.com/css2?family=Poppins:wght@400;500;700;800&display=swap">
<style>
  :root {
    --backdrop: #c9c9c9;
    --brand-red: #b01e28;
    --deep-red: #5a1017;
    --navy: #1b2b4b;
    --ink: #1e1e1e;
    --paper: #ffffff;
  }
  * { box-sizing: border-box; margin: 0; padding: 0; }
  html, body {
    width: 1200px; height: 1015px; overflow: hidden;
    background: var(--backdrop);
    font-family: "Poppins", sans-serif;
  }
  .canvas {
    position: relative; width: 1200px; height: 1015px;
    display: flex; flex-direction: column; align-items: center; justify-content: center; gap: 56px;
  }
  .card {
    position: relative; width: 660px; height: 378px;
    box-shadow: 0 14px 28px rgba(0,0,0,.28);
  }
  .card--front {
    background: var(--brand-red);
    display: flex; align-items: center; justify-content: center;
  }
  .wordmark {
    font-weight: 800; letter-spacing: -2px; line-height: 1; white-space: nowrap;
  }
  .card--front .wordmark { font-size: 84px; color: var(--deep-red); }

  .card--back { background: var(--paper); }
  .card--back .wordmark {
    position: absolute; top: 54px; right: 46px;
    font-size: 48px; color: var(--brand-red);
  }
  .identity {
    position: absolute; top: 140px; left: 48px;
    padding-left: 16px; border-left: 4px solid var(--navy);
  }
  .identity__name { font-size: 30px; font-weight: 700; color: var(--brand-red); line-height: 1.1; }
  .identity__title { font-size: 20px; font-weight: 400; color: var(--navy); line-height: 1.2; }

  .contacts {
    position: absolute; top: 232px; left: 68px; list-style: none;
  }
  .contacts li {
    display: flex; align-items: center; gap: 12px;
    font-size: 18px; color: var(--ink); line-height: 28px;
  }
  .contacts svg { width: 18px; height: 18px; flex: none; fill: none; stroke: var(--brand-red); stroke-width: 2; }

  .address {
    position: absolute; left: 340px; bottom: 40px;
    font-size: 18px; color: var(--ink); line-height: 1.35; font-style: normal;
  }
</style>
</head>
<body>
<main class="canvas">
  <section class="card card--front" aria-label="Card front">
    <span class="wordmark">Veltrane Group</span>
  </section>

  <section class="card card--back" aria-label="Card back">
    <span class="wordmark">Veltrane Group</span>

    <div class="identity">
      <p class="identity__name">Rohesh Kamdar</p>
      <p class="identity__title">CEO</p>
    </div>

    <ul class="contacts">
      <li>
        <svg viewBox="0 0 24 24" aria-hidden="true"><path d="M5 3h4l2 5-2.5 1.5a11 11 0 0 0 6 6L16 13l5 2v4a2 2 0 0 1-2 2A17 17 0 0 1 3 5a2 2 0 0 1 2-2z"/></svg>
        604.781.2249
      </li>
      <li>
        <svg viewBox="0 0 24 24" aria-hidden="true"><rect x="3" y="5" width="18" height="14" rx="1"/><path d="M3 6l9 7 9-7"/></svg>
        roheshkamdar@veltrane.com
      </li>
      <li>
        <svg viewBox="0 0 24 24" aria-hidden="true"><circle cx="12" cy="12" r="9"/><path d="M3 12h18M12 3c3 3 3 15 0 18M12 3c-3 3-3 15 0 18"/></svg>
        www.veltrane.com
      </li>
    </ul>

    <address class="address">4180 Lindqvist Ave, Tampa<br>FL 33482</address>
  </section>
</main>
</body>
</html>
```